Local Flower Farm Needs Business Card Design

I need business cards designed for a flower farm based in Eudora, Kansas.
Business Info:
We are a local cut flower farm located in Eudora, Kansas, founded by Corinne Haldwick. What started as a passion for agriculture and search for more joy in daily life has blossomed into a small business dedicated to providing the community with beautiful, fresh, and sustainable flowers. We specialize in local, seasonal blooms, ensuring that every petal reflects the care and dedication we pour into our craft. Our mission is to deliver the highest quality flowers directly to our customers through local farmers markets and to florists who share our commitment to sustainability. Join us in celebrating the beauty of nature, one bloom at a time!
Contact Details:
Corinne Haldwick
Owner
Phone 913-555-0147
Facebook: Rosalind Thorpe Gardens
Instagram: @RosalindThorpeGardens
Website: RosalindThorpeGardens.example
Target Market(s)
Wholesale to Florists and Direct to Consumer via Farmers Market
Industry/Entity Type
Florist, Farm
Contact Information for Business Card
Name, Contact Info, Logo
Look and feel
Each slider illustrates characteristics of the customer's brand and the style your logo design should communicate.

```html
<!DOCTYPE html>
<html lang="en">
<head>
<meta charset="utf-8">
<title>Rosalind Thorpe Gardens — Business Card</title>
<link href="https://fonts.googleapis.com/css2?family=Cormorant+Garamond:wght@500&family=Roboto:wght@400;700&display=swap" rel="stylesheet">
<style>
  :root {
    --backdrop: #1e2022;
    --card-teal: #0f3a3d;
    --card-teal-deep: #0a2b2e;
    --ink-light: #ffffff;
    --ink-soft: #dfe8e8;
    --rule-soft: rgba(255,255,255,0.75);
    --watermark: rgba(140,180,180,0.10);
  }
  * { margin: 0; padding: 0; box-sizing: border-box; }
  html, body { width: 1200px; height: 900px; overflow: hidden; }
  body {
    background: var(--backdrop);
    position: relative;
    font-family: "Roboto", Arial, sans-serif;
  }
  .card {
    position: absolute;
    left: 300px;
    width: 600px;
    height: 343px;
    background: linear-gradient(160deg, var(--card-teal) 0%, var(--card-teal-deep) 100%);
    border-radius: 4px;
    overflow: hidden;
  }
  .card--back { top: 70px; }
  .card--front { top: 470px; }

  .brand-seal {
    position: absolute;
    border: 1.5px solid var(--rule-soft);
    border-radius: 50%;
    display: flex;
    align-items: center;
    justify-content: center;
    text-align: center;
    color: var(--ink-light);
    font-family: "Cormorant Garamond", Georgia, serif;
    font-weight: 500;
    letter-spacing: 0.08em;
    text-transform: uppercase;
    line-height: 1.25;
  }
  .card--back .brand-seal {
    width: 150px; height: 150px;
    left: 225px; top: 96px;
    font-size: 17px;
  }
  .card--front .brand-seal {
    width: 112px; height: 112px;
    left: 34px; top: 26px;
    font-size: 13px;
  }

  .brand-watermark {
    position: absolute;
    left: 190px; top: 40px;
    width: 260px;
    color: var(--watermark);
    font-family: "Cormorant Garamond", Georgia, serif;
    font-weight: 500;
    font-size: 78px;
    line-height: 0.95;
    text-transform: uppercase;
    text-align: center;
    pointer-events: none;
  }

  .contact-list {
    position: absolute;
    left: 34px; top: 160px;
    list-style: none;
    color: var(--ink-soft);
    font-size: 15px;
    line-height: 24px;
  }
  .contact-list li { display: flex; align-items: center; gap: 8px; }
  .contact-icon { width: 11px; height: 11px; flex: none; }

  .person {
    position: absolute;
    right: 44px; top: 200px;
    text-align: right;
    color: var(--ink-light);
  }
  .person__name {
    font-weight: 700;
    font-size: 24px;
    letter-spacing: 0.01em;
    text-transform: uppercase;
  }
  .person__role {
    font-size: 15px;
    margin-top: 4px;
  }
</style>
</head>
<body>
  <section class="card card--back" aria-label="Card back">
    <div class="brand-seal">Rosalind<br>Thorpe<br>Gardens</div>
  </section>

  <section class="card card--front" aria-label="Card front">
    <div class="brand-watermark" aria-hidden="true">Rosalind Thorpe</div>
    <div class="brand-seal">Rosalind<br>Thorpe<br>Gardens</div>
    <ul class="contact-list">
      <li>
        <svg class="contact-icon" viewBox="0 0 24 24" aria-hidden="true"><path fill="#fff" d="M6.6 10.8c1.4 2.8 3.8 5.1 6.6 6.6l2.2-2.2c.3-.3.7-.4 1-.2 1.1.4 2.3.6 3.6.6.6 0 1 .4 1 1V20c0 .6-.4 1-1 1C10.6 21 3 13.4 3 4c0-.6.4-1 1-1h3.5c.6 0 1 .4 1 1 0 1.3.2 2.5.6 3.6.1.3 0 .7-.2 1L6.6 10.8z"/></svg>
        913-555-0147
      </li>
      <li><svg class="contact-icon" viewBox="0 0 12 12" aria-hidden="true"><circle cx="6" cy="6" r="5.5" fill="#fff"/></svg>Rosalind Thorpe Gardens</li>
      <li><svg class="contact-icon" viewBox="0 0 12 12" aria-hidden="true"><circle cx="6" cy="6" r="5.5" fill="#fff"/></svg>@RosalindThorpeGardens</li>
      <li><svg class="contact-icon" viewBox="0 0 12 12" aria-hidden="true"><circle cx="6" cy="6" r="5.5" fill="#fff"/></svg>RosalindThorpeGardens.example</li>
    </ul>
    <div class="person">
      <p class="person__name">Corinne Haldwick</p>
      <p class="person__role">Owner</p>
    </div>
  </section>
</body>
</html>
```